The Neighbors Together Project

For submission to Lantern Campaign 2024
Need both Color and Black and White Versions
TITLE The Neighbors Together Project
Slogan; "Neighbors Together, one road...one Heart, just a different stride" -JT Pellow copyrights
Logo in Color and Logo in Black and White
Back of flyer will be The Field of Quiet Lanterns poem -JT Pellow
VOTE BLUE 2024 Header or Footer

I just want to thank you all for your participation in The Neighbors Together Project. In the next few days I will be reducing the choices down to 10. Id like for all of you to know Ive enjoyed seeing so many options and views on the Flyer. Mainly, I wanted to say to those who don't make the cut that I appreciate the work you've done.

LM Dorsey

```html
<!DOCTYPE html>
<html lang="en">
<head>
<meta charset="utf-8">
<title>The Neighbors Together Project – Flyer</title>
<link rel="stylesheet" href="https://fonts.googleapis.com/css2?family=Alfa+Slab+One&family=Archivo+Black&family=Roboto:wght@400;500&display=swap">
<style>
  :root {
    --navy: #1d2f7a;
    --blue: #2b48b8;
    --red: #d42630;
    --white: #ffffff;
    --ink: #1b1b1b;
    --stage: #e9e9ec;
  }
  * { box-sizing: border-box; margin: 0; padding: 0; }
  html, body { width: 1200px; height: 1200px; overflow: hidden; }
  body {
    background: var(--stage);
    font-family: "Roboto", Arial, sans-serif;
    display: flex;
    align-items: center;
    justify-content: center;
    gap: 60px;
  }
  .flyer {
    width: 520px;
    height: 740px;
    background: var(--white);
    display: flex;
    flex-direction: column;
    box-shadow: 0 6px 18px rgba(0,0,0,0.15);
  }
  .band-red { background: var(--red); height: 22px; }
  .band-red.thin { height: 8px; }
  .vote-bar {
    background: var(--blue);
    color: var(--white);
    font-family: "Alfa Slab One", Georgia, serif;
    font-size: 34px;
    letter-spacing: 2px;
    text-align: center;
    height: 62px;
    line-height: 62px;
  }
  .flyer-body { flex: 1; display: flex; flex-direction: column; align-items: center; }

  /* Front */
  .front .flyer-body { padding: 54px 40px 30px; justify-content: center; }
  .project-name {
    font-family: "Archivo Black", Arial, sans-serif;
    color: var(--navy);
    font-size: 30px;
    text-align: center;
    line-height: 1.15;
    text-transform: uppercase;
    margin-bottom: 22px;
  }
  .emblem-art {
    width: 360px;
    height: 230px;
    border-radius: 10px;
    background: linear-gradient(135deg, var(--red) 0%, #f1f1f4 50%, var(--navy) 100%);
  }
  .tagline {
    font-family: "Archivo Black", Arial, sans-serif;
    color: var(--red);
    font-size: 18px;
    text-transform: uppercase;
    margin-top: 14px;
  }
  .tagline.first { margin-top: 20px; }
  .stride {
    font-family: "Archivo Black", Arial, sans-serif;
    color: var(--navy);
    font-size: 30px;
    text-transform: uppercase;
    margin-top: 20px;
    text-align: center;
  }

  /* Back */
  .back .flyer-body { padding: 26px 30px 18px; }
  .poem-title, .poem-byline {
    font-family: "Archivo Black", Arial, sans-serif;
    color: var(--ink);
    font-size: 22px;
    text-align: center;
    line-height: 1.2;
  }
  .poem {
    margin-top: 18px;
    font-size: 14px;
    line-height: 2;
    color: var(--ink);
    text-align: center;
  }
  .web-link {
    margin-top: auto;
    color: var(--blue);
    font-weight: 500;
    font-size: 15px;
  }
</style>
</head>
<body>

  <section class="flyer front">
    <div class="band-red"></div>
    <div class="flyer-body">
      <h1 class="project-name">Neighbors Together Project</h1>
      <div class="emblem-art" role="img" aria-label="Illustration of a flag-patterned country map with a chain of paper-doll figures in different shades holding hands"></div>
      <p class="tagline first">One road...</p>
      <p class="tagline">One heart...</p>
      <p class="stride">Just a different stride</p>
    </div>
    <div class="band-red thin"></div>
    <div class="vote-bar">VOTE BLUE 2024</div>
  </section>

  <section class="flyer back">
    <div class="band-red"></div>
    <div class="vote-bar">VOTE BLUE 2024</div>
    <div class="flyer-body">
      <h2 class="poem-title">The Field of Quiet Lanterns</h2>
      <p class="poem-byline">By JT Pellow</p>
      <p class="poem">
        Morning fog lifts slowly from a field of quiet lanterns,<br>
        each one lit by a different hand along the fence line.<br>
        Some glow amber, some glow pale, some flicker green and low,<br>
        yet every flame is leaning toward the same wide sky.<br>
        A baker sets hers down beside a welder's, then a nurse's,<br>
        a farmer's next to a student's, a grandmother's by a child's.<br>
        No single lantern lights the road for everyone who walks it,<br>
        but set together, row by row, the dark gives way.<br>
        So bring your light, however small, and place it with the others;<br>
        the field is only bright when all of us are here.
      </p>
      <p class="web-link">www.neighborstogetherproject.org</p>
    </div>
    <div class="band-red thin"></div>
    <div class="vote-bar">VOTE BLUE 2024</div>
  </section>

</body>
</html>
```